Card design for orthopaedic surgeons working as The Brightwater Joint Centre

Business cards, letterhead

Colors

Designer to choose colors to be used in the design.

Requirements
Must have
• Late addition.
• Cards letterhead must have logos of
• Crestmoor Lindell College of Surgeons
• Varenwood Bone Health Association
Nice to have
• Back of card to have space for appointment time to be added by hand and some blank space for writing incidental other notes.

```html
<!DOCTYPE html>
<html lang="en">
<head>
<meta charset="utf-8">
<title>The Brightwater Joint Centre – Business Card</title>
<link href="https://fonts.googleapis.com/css2?family=Lato:ital,wght@0,400;0,700;1,400&display=swap" rel="stylesheet">
<style>
  :root {
    --navy: #053a54;
    --sky: #1fa3df;
    --ink: #2a2a2a;
    --paper: #ffffff;
    --stage: #e9edf0;
  }
  html, body {
    margin: 0;
    width: 1200px;
    height: 780px;
    overflow: hidden;
    background: var(--stage);
    font-family: "Lato", Arial, sans-serif;
  }
  .sheet {
    width: 1200px;
    height: 780px;
    display: flex;
    align-items: center;
    justify-content: center;
    gap: 40px;
  }
  .card {
    width: 560px;
    height: 320px;
    border-radius: 18px;
    overflow: hidden;
    box-shadow: 0 6px 18px rgba(0,0,0,0.18);
  }
  .card svg { display: block; }
  .brand-name { font-family: "Lato", Arial, sans-serif; font-weight: 400; font-size: 31px; }
  .person-name { font-family: "Lato", Arial, sans-serif; font-weight: 700; font-size: 22px; fill: var(--sky); letter-spacing: 0.5px; }
  .person-role { font-family: "Lato", Arial, sans-serif; font-style: italic; font-size: 15px; fill: var(--ink); }
  .address { font-family: "Lato", Arial, sans-serif; font-style: italic; font-size: 15px; fill: var(--paper); }
  .contact { font-family: "Lato", Arial, sans-serif; font-size: 15px; fill: var(--ink); }
  .icon { fill: var(--ink); }
</style>
</head>
<body>
<main class="sheet">

  <!-- Card back -->
  <section class="card card-back" aria-label="Card back">
    <svg width="560" height="320" viewBox="0 0 560 320">
      <rect class="back-fill" width="560" height="320" fill="var(--navy)"/>
      <text class="brand-name" x="40" y="120" fill="var(--paper)">The Brightwater Joint Centre</text>
    </svg>
  </section>

  <!-- Card front -->
  <section class="card card-front" aria-label="Card front">
    <svg width="560" height="320" viewBox="0 0 560 320">
      <rect width="560" height="320" fill="var(--paper)"/>
      <text class="brand-name" x="110" y="66" fill="var(--sky)">The Brightwater Joint Centre</text>

      <text class="person-name" x="34" y="128">JORDAN HALE</text>
      <text class="person-role" x="34" y="150">CEO/Founder</text>

      <path class="footer-band" d="M0,196 H300 L342,282 H560 V320 H0 Z" fill="var(--navy)"/>
      <path class="footer-stripe" d="M318,258 H560 V272 H325 Z" fill="var(--sky)"/>

      <text class="address" x="26" y="228">West 18th Avenue</text>
      <text class="address" x="26" y="252">Suite 310, Harborview, HV 20418</text>

      <g class="contacts">
        <text class="contact" x="512" y="160" text-anchor="end">+0044 55 66 77 88</text>
        <text class="contact" x="512" y="182" text-anchor="end">+0044 55 66 77 88</text>
        <text class="contact" x="512" y="204" text-anchor="end">info@brightwaterjoint.com</text>
        <text class="contact" x="512" y="226" text-anchor="end">www.brightwaterjoint.com</text>

        <path class="icon icon-phone" d="M521,150 c1,-1 3,-1 4,1 l1,3 c0,1 -1,2 -2,2 c1,2 2,3 4,4 c0,-1 1,-2 2,-2 l3,1 c2,1 2,3 1,4 c-6,2 -14,-6 -13,-13 z"/>
        <rect class="icon icon-mobile" x="524" y="170" width="8" height="13" rx="1.5" fill="none" stroke="var(--ink)" stroke-width="1.8"/>
        <g class="icon-mail">
          <rect x="521" y="194" width="14" height="10" fill="var(--ink)"/>
          <path d="M521,194 L528,200 L535,194" fill="none" stroke="var(--paper)" stroke-width="1.2"/>
        </g>
        <g class="icon-globe" fill="none" stroke="var(--ink)" stroke-width="1.4">
          <circle cx="528" cy="221" r="6.5" fill="var(--ink)"/>
          <ellipse cx="528" cy="221" rx="2.8" ry="6.5" stroke="var(--paper)" stroke-width="0.9"/>
          <line x1="521.5" y1="221" x2="534.5" y2="221" stroke="var(--paper)" stroke-width="0.9"/>
        </g>
      </g>
    </svg>
  </section>

</main>
</body>
</html>
```